Designer Instructions – Updated Referral Program Flyer

(Based on the mock-up in “Brief Layout and Instructions.pdf”)

OVERALL STYLE + LAYOUT

Maintain the same general layout, structure, and flow as the mock-up flyer (front and back).

This is an update of an older flyer, not a full redesign — keep the same sections, proportions, and overall visual feel, but with cleaner, more modern design improvements.

The final flyer should look clean, bold, professional, and high-impact, geared toward realtors, property managers, and contractors who refer work.

FRONT SIDE INSTRUCTIONS
1. Header Section

Remove the Rebuild Harbor Crest logo from the top banner.
(Shown on page 1 of the PDF)

2. Main Headline

Keep the same three-line structure:
EARN
UNLIMITED
CASH

Center it, maximize impact, and increase the font size of CASH so all three words match in importance.

Make the headline bold, clean, and the main focal point.

3. Cash Incentive Box

Keep the "$500 minimum OR 10% per referral" box, but upgrade the graphics to look sharper and more modern.

Ensure the wording matches exactly what’s in the mock-up.

4. Premier Partner Program Ribbon

Clean up and modernize the "PREMIER PARTNER PROGRAM" bar while keeping the same position and structure.

Ensure the checkmark badge remains crisp and professional.

5. Supporting Icons Section

Keep the four icons/benefit boxes (Guaranteed Payout, Free Evaluations, Affordable Solutions, Industry Leaders) in the same order.

Update the icons to cleaner, more modern styles — but maintain the same meanings.

Improve alignment and spacing for sharper visual consistency.

6. Remove Icons in Contact Area

At the bottom (“CALL TEXT OR BOOK ONLINE 858-471-6093 BrightlaneRenovate.com”), remove the phone and internet icons, as noted on page 2 of the PDF.

7. Replace All Images

I (Dorian) will provide all updated stock images separately via email.

Replace the flood/water-damage imagery and roof leak with the new images I send.

Keep image placement and proportions the same as the mock-up.

BACK SIDE INSTRUCTIONS
1. Header Image + “REFER / EARN” Section

Maintain the same large split-image layout (“The more you refer, the more you earn”).

Replace all background imagery with the new assets I will send.

Keep the CASH FLOW image section but modernize the type and spacing.

2. “HOW IT WORKS” Section

Preserve the three-column layout:

Refer Flood, Water & Mold Damage

We Take Care of Everything (evaluations/insurance)

Get Paid to Share

Update images, tighten spacing, and use modern iconography.

3. Remove Phone/Internet Icons

Same as the front side — remove small communication icons and keep only the text/number/URL.

4. Bottom Contact Bar

Keep the blue bar, same wording, same layout — just modernize the style if needed for clarity.

5. Replace All Back-Side Images

Again, I will email you the image assets.

Keep the layout EXACT — just update with higher-quality photos and improved design.

TEXT CONTENT (Keep as-is unless spacing adjustments needed)

All text shown in the PDF should remain exactly the same unless spacing or visual balance requires minor adjustments.
Example from page 3:

“REFER FLOOD, MOLD & CONSTRUCTION JOBS”

“We Schedule a Free Estimate. If Approved, You Get Paid.”

“Everybody Benefits From Referrals”

Everything stays, just refreshed and visually improved.

DESIGN GOALS

Flyer should look high-end and trustworthy, not salesy.

Consistent color theme: blues, whites, yellows, same palette as original.

Use bold, modern fonts with strong readability.

Ensure all headlines pop and all benefit boxes are clean, well-aligned, and evenly spaced.

The final result should feel like a premium referral program flyer for a top-tier restoration/remodel company.

FILES I WILL PROVIDE

I will send the designer:

All replacement stock photos

Any updated logos (if needed)

Original high-resolution version of the mock-up (if available)

Any additional icons preferred

Colors
0054AA
0677BA
7BADD7
CADEEF
E8F1F8

Requirements
Must have
• Designer Instructions – Updated Referral Program Flyer (Based on the mock-up in “Brief Layout and Instructions.pdf”) OVERALL STYLE + LAYOUT Maintain the same general layout, structure, and flow as the mock-up flyer (front and back). This is an update of an older flyer, not a full redesign — keep the same sections, proportions, and overall visual feel, but with cleaner, more modern design improvements. The final flyer should look clean, bold, professional, and high-impact, geared toward realtors, property managers, and contractors who refer work. FRONT SIDE INSTRUCTIONS 1. Header Section Remove the Rebuild Harbor Crest logo from the top banner. (Shown on page 1 of the PDF) 2. Main Headline Keep the same three-line structure: EARN UNLIMITED CASH Center it, maximize impact, and increase the font size of CASH so all three words match in importance. Make the headline bold, clean, and the main focal point. 3. Cash Incentive Box Keep the "$500 minimum OR 10% per referral" box, but upgrade the graphics to look sharper and more modern. Ensure the wording matches exactly what’s in the mock-up. 4. Premier Partner Program Ribbon Clean up and modernize the "PREMIER PARTNER PROGRAM" bar while keeping the same position and structure. Ensure the checkmark badge remains crisp and professional. 5. Supporting Icons Section Keep the four icons/benefit boxes (Guaranteed Payout, Free Evaluations, Affordable Solutions, Industry Leaders) in the same order. Update the icons to cleaner, more modern styles — but maintain the same meanings. Improve alignment and spacing for sharper visual consistency. 6. Remove Icons in Contact Area At the bottom (“CALL TEXT OR BOOK ONLINE 858-471-6093 BrightlaneRenovate.com”), remove the phone and internet icons, as noted on page 2 of the PDF. 7. Replace All Images I (Dorian) will provide all updated stock images separately via email. Replace the flood/water-damage imagery and roof leak with the new images I send. Keep image placement and proportions the same as the mock-up. BACK SIDE INSTRUCTIONS 1. Header Image + “REFER / EARN” Section Maintain the same large split-image layout (“The more you refer, the more you earn”). Replace all background imagery with the new assets I will send. Keep the CASH FLOW image section but modernize the type and spacing. 2. “HOW IT WORKS” Section Preserve the three-column layout: Refer Flood, Water & Mold Damage We Take Care of Everything (evaluations/insurance) Get Paid to Share Update images, tighten spacing, and use modern iconography. 3. Remove Phone/Internet Icons Same as the front side — remove small communication icons and keep only the text/number/URL. 4. Bottom Contact Bar Keep the blue bar, same wording, same layout — just modernize the style if needed for clarity. 5. Replace All Back-Side Images Again, I will email you the image assets. Keep the layout EXACT — just update with higher-quality photos and improved design. TEXT CONTENT (Keep as-is unless spacing adjustments needed) All text shown in the PDF should remain exactly the same unless spacing or visual balance requires minor adjustments. Example from page 3: “REFER FLOOD, MOLD & CONSTRUCTION JOBS” “We Schedule a Free Estimate. If Approved, You Get Paid.” “Everybody Benefits From Referrals” Everything stays, just refreshed and visually improved. DESIGN GOALS Flyer should look high-end and trustworthy, not salesy. Consistent color theme: blues, whites, yellows, same palette as original. Use bold, modern fonts with strong readability. Ensure all headlines pop and all benefit boxes are clean, well-aligned, and evenly spaced. The final result should feel like a premium referral program flyer for a top-tier restoration/remodel company. FILES I WILL PROVIDE I will send the designer: All replacement stock photos Any updated logos (if needed) Original high-resolution version of the mock-up (if available) Any additional icons preferred

```html
<!DOCTYPE html>
<html lang="en">
<head>
<meta charset="utf-8">
<title>Referral Program Flyer</title>
<link href="https://fonts.googleapis.com/css2?family=League+Gothic&family=Poppins:wght@400;500;600;700;800&display=swap" rel="stylesheet">
<style>
  :root{
    --stage:#8a8c99;
    --navy:#0c2a5e;
    --royal:#0a3187;
    --red:#e2272d;
    --yellow:#f9e11a;
    --orange:#fb8a1e;
    --slate:#7d8c99;
    --panel:#eef2f7;
    --bar:#e7eaf0;
    --white:#ffffff;
    --ink:#13294f;
  }
  *{box-sizing:border-box;margin:0;padding:0}
  html,body{width:841px;height:1200px;overflow:hidden}
  body{background:var(--stage);font-family:"Poppins",sans-serif;color:var(--ink);position:relative}
  .flyer{position:absolute;left:91.5px;width:658.6px;height:509px;background:var(--white);overflow:hidden;box-shadow:0 6px 18px rgba(0,0,0,.25)}
  .flyer--front{top:62.7px}
  .flyer--back{top:628.8px}
  .hero{position:absolute;left:0;top:0;width:100%;height:248px;background:var(--navy)}
  .hero__frame{position:absolute;top:0;left:306px;right:0;height:248px;background:var(--white);
    clip-path:polygon(64px 0,100% 0,100% 100%,64px 100%,0 50%)}
  .hero__photo{position:absolute;top:0;left:313.6px;right:0;height:248px;
    clip-path:polygon(57.4px 0,100% 0,100% 100%,57.4px 100%,0 50%)}
  .hero__photo--kitchen{background:linear-gradient(160deg,#eef1f5 0%,#d6e1ea 45%,#9fbdd3 100%)}
  .hero__photo--money{background:linear-gradient(135deg,#dfe1dc 0%,#b9beb6 50%,#e5e7e2 100%)}

  .headline{position:absolute;left:0;width:324px;text-align:center;font-weight:800;line-height:1;white-space:nowrap}
  .headline--earn{top:35px;font-size:60px;color:var(--yellow)}
  .headline--unlimited{top:94px;font-size:50px;color:var(--white);letter-spacing:-1.5px}
  .headline--cash{top:138px;font-size:66px;color:var(--yellow)}

  .incentive{position:absolute;left:42px;top:262.4px;width:305px;height:47px;background:var(--red);border-radius:24px;color:var(--white)}
  .incentive__min{position:absolute;left:32px;top:3px;text-align:center;line-height:1}
  .incentive__amount{font-size:25px;font-weight:700}
  .incentive__amount sup{font-size:11px;vertical-align:11px}
  .incentive__label{font-size:11.5px;font-weight:500;display:block;margin-top:1px}
  .incentive__or{position:absolute;left:98px;top:-4px;width:55px;height:55px;border-radius:50%;background:var(--royal);border:3px solid var(--white);
    display:flex;align-items:center;justify-content:center;font-weight:700;font-size:17px}
  .incentive__pct{position:absolute;left:159px;top:4px;font-size:33px;font-weight:700;line-height:1.1}
  .incentive__per{position:absolute;left:224px;top:9px;font-size:12px;font-weight:500;line-height:1.2}

  .program{position:absolute;left:380px;top:270px;width:238px;height:30px;display:flex;align-items:center;justify-content:center;gap:9px}
  .program__dot{width:14px;height:14px;border-radius:50%;background:var(--red)}
  .program__name{font-size:17px;font-weight:700;color:var(--red);letter-spacing:.8px}

  .benefits{position:absolute;top:343px;left:0;width:100%}
  .benefit{position:absolute;top:0;width:127px;height:103px;background:var(--panel);border:1.5px solid var(--royal);border-radius:7px;text-align:center}
  .benefit__icon{position:absolute;left:43.5px;top:-19px;width:40px;height:40px;border-radius:50%;background:var(--royal);border:2px solid var(--white)}
  .benefit__icon svg{width:100%;height:100%}
  .benefit__title{position:absolute;left:12.5px;top:29px;width:102px;height:33px;border-radius:17px;background:var(--royal);color:var(--white);
    font-size:9.5px;font-weight:600;line-height:1.2;display:flex;align-items:center;justify-content:center}
  .benefit__text{position:absolute;left:0;right:0;top:69px;font-size:8.2px;line-height:1.35;color:var(--ink)}
  .accent-red{color:var(--red);font-weight:600}

  .contact{position:absolute;left:0;bottom:0;width:100%;height:41px;background:var(--bar)}
  .contact__cta{position:absolute;left:0;top:0;width:271px;height:41px;background:var(--navy);clip-path:polygon(0 0,250px 0,100% 100%,0 100%);
    color:var(--white);font-size:14.3px;font-weight:500;display:flex;align-items:center;padding-left:29px;white-space:nowrap}
  .contact__phone{position:absolute;left:284px;top:0;height:41px;display:flex;align-items:center;font-size:17px;font-weight:700;color:var(--navy)}
  .contact__phone span{font-weight:500;margin-right:5px}
  .contact__rule{position:absolute;left:448px;top:12px;width:1px;height:17px;background:var(--slate)}
  .contact__web{position:absolute;left:461px;top:0;height:41px;display:flex;align-items:center;font-size:11.5px;font-weight:500;color:var(--navy)}

  .slogan{position:absolute;left:0;width:318px;text-align:center;font-family:"League Gothic",sans-serif;line-height:.86;white-space:nowrap;transform:scaleX(1.16);transform-origin:157px 0}
  .slogan--small{font-size:31px;color:var(--white)}
  .slogan--big{background:linear-gradient(180deg,var(--yellow) 30%,var(--orange) 100%);-webkit-background-clip:text;background-clip:text;color:transparent}
  .slogan--l1{top:28px}
  .slogan--l2{top:52px;font-size:76px}
  .slogan--l3{top:114px}
  .slogan--l4{top:139px;font-size:92px}
  .hero__shade{position:absolute;left:80px;top:40px;width:300px;height:208px;background:linear-gradient(135deg,rgba(5,15,40,.55),rgba(5,15,40,0) 70%);
    clip-path:polygon(0 0,30% 0,100% 70%,100% 100%,45% 100%,0 60%)}

  .steps-ribbon{position:absolute;left:0;top:235px;width:225px;height:23px;background:var(--yellow);clip-path:polygon(0 0,212px 0,100% 100%,0 100%);
    color:var(--navy);font-weight:700;font-size:13px;display:flex;align-items:center;padding-left:78px}
  .step{position:absolute;top:270px;width:150.5px;height:163px;border:1.5px solid var(--royal);border-radius:7px;overflow:hidden;text-align:center;background:var(--white)}
  .step__photo{height:83px;border-bottom:1px solid #d7dde6}
  .step__photo--pipe{background:linear-gradient(180deg,#f1f1ef,#c9c8c3)}
  .step__photo--estimate{background:linear-gradient(180deg,#c6d6e4 0%,#7e9bb4 60%,#5d7a46 100%)}
  .step__photo--sign{background:linear-gradient(180deg,#5f8fd0 0%,#cfe0f3 70%,#eef3f9 100%)}
  .step__title{margin-top:10px;font-size:11.2px;font-weight:600;line-height:1.3;color:var(--navy)}
  .step__text{margin-top:6px;font-size:9.3px;line-height:1.4;color:var(--ink)}
  .accent-blue{color:#1d5bd6}
  .refer-line{position:absolute;left:0;width:100%;top:442px;text-align:center;font-size:14px;font-weight:700;color:var(--navy)}
  .refer-line span{color:var(--red)}
</style>
</head>
<body>

<section class="flyer flyer--front">
  <div class="hero">
    <h1 class="headline headline--earn">EARN</h1>
    <div class="headline headline--unlimited">UNLIMITED</div>
    <div class="headline headline--cash">CASH</div>
    <div class="hero__frame"></div>
    <div class="hero__photo hero__photo--kitchen" role="img" aria-label="Photo of a bright white kitchen with water pouring through a broken ceiling"></div>
  </div>

  <div class="incentive">
    <div class="incentive__min"><span class="incentive__amount"><sup>$</sup>500</span><span class="incentive__label">MINIMUM</span></div>
    <div class="incentive__or">OR</div>
    <div class="incentive__pct">10%</div>
    <div class="incentive__per">PER<br>REFERRAL</div>
  </div>

  <div class="program">
    <span class="program__dot"></span>
    <span class="program__name">PARTNER PROGRAM</span>
  </div>

  <div class="benefits">
    <div class="benefit" style="left:44px">
      <div class="benefit__icon"><svg viewBox="0 0 40 40" fill="none" stroke="#fff" stroke-width="1.6" stroke-linecap="round" stroke-linejoin="round"><rect x="12" y="10" width="16" height="9" rx="1"/><circle cx="20" cy="14.5" r="2"/><path d="M9 27 h5 l5 2 h6 c2 0 2-3 0-3 h-5 M14 27 v-3 h5 l4 2"/></svg></div>
      <div class="benefit__title">GUARANTEED<br>PAYOUT</div>
      <p class="benefit__text">Minimum <span class="accent-red">$500</span> or <span class="accent-red">10%</span> of<br>Total Invoice Paid Fast</p>
    </div>
    <div class="benefit" style="left:192px">
      <div class="benefit__icon"><svg viewBox="0 0 40 40" fill="none" stroke="#fff" stroke-width="1.6" stroke-linecap="round" stroke-linejoin="round"><rect x="13" y="9" width="14" height="20" rx="1.5"/><path d="M16 13 h8 M16 17 h8 M16 21 h5 M11 14 v14 h2"/></svg></div>
      <div class="benefit__title">FREE<br>ESTIMATES</div>
      <p class="benefit__text">Fast &amp; Free Inspections &amp;<br>Written Estimates</p>
    </div>
    <div class="benefit" style="left:340px">
      <div class="benefit__icon"><svg viewBox="0 0 40 40" fill="none" stroke="#fff" stroke-width="1.6" stroke-linecap="round" stroke-linejoin="round"><path d="M16 20 a6 6 0 1 1 8 0 v2 h-8 z M17 24 h6"/><path d="M20 12 v6 M18.5 13.5 h2.5 a1 1 0 0 1 0 2 h-2 a1 1 0 0 0 0 2 h2.5"/><path d="M9 29 h4 l4 1.5 h5 l5-3"/></svg></div>
      <div class="benefit__title">AFFORDABLE<br>SOLUTIONS</div>
      <p class="benefit__text">Lowest Out of Pocket<br>Costs for Your Customers</p>
    </div>
    <div class="benefit" style="left:487px">
      <div class="benefit__icon"><svg viewBox="0 0 40 40" fill="none" stroke="#fff" stroke-width="1.6" stroke-linecap="round" stroke-linejoin="round"><circle cx="20" cy="14" r="3"/><path d="M15 22 a5 5 0 0 1 10 0"/><circle cx="12" cy="21" r="2.3"/><path d="M8 28 a4 4 0 0 1 8 0"/><circle cx="28" cy="21" r="2.3"/><path d="M24 28 a4 4 0 0 1 8 0"/></svg></div>
      <div class="benefit__title">INDUSTRY<br>LEADERS</div>
      <p class="benefit__text">Licensed &amp; Certified Experts<br>Provide 100% Guarantee</p>
    </div>
  </div>

  <footer class="contact">
    <div class="contact__cta">CALL, TEXT OR BOOK ON-LINE</div>
    <div class="contact__phone"><span>NE</span>858-471-6093</div>
    <div class="contact__rule"></div>
    <div class="contact__web">www.BrightlaneRenovate.com</div>
  </footer>
</section>

<section class="flyer flyer--back">
  <div class="hero">
    <div class="hero__shade"></div>
    <div class="slogan slogan--small slogan--l1">THE MORE YOU</div>
    <div class="slogan slogan--big slogan--l2">REFER</div>
    <div class="slogan slogan--small slogan--l3">THE MORE YOU</div>
    <div class="slogan slogan--big slogan--l4">EARN</div>
    <div class="hero__frame"></div>
    <div class="hero__photo hero__photo--money" role="img" aria-label="Photo of hundred-dollar bills with letter tiles spelling CASH FLOW"></div>
  </div>
  <div class="steps-ribbon">HOW IT WORK'S</div>

  <div class="step" style="left:78px">
    <div class="step__photo step__photo--pipe" role="img" aria-label="Photo of a leaking pipe under a sink"></div>
    <div class="step__title">REFER FLOOD, MOLD &amp;<br>CONSTRUCTION JOBS</div>
    <p class="step__text">It's Simple to Refer <span class="accent-blue">24/7</span><br>Call, Text or Book Online</p>
  </div>
  <div class="step" style="left:253.5px">
    <div class="step__photo step__photo--estimate" role="img" aria-label="Photo of a clipboard with a work estimate in front of a house"></div>
    <div class="step__title">WE TAKE CARE OF<br>EVERYTHING</div>
    <p class="step__text">We Schedule a Free Estimate.<br>If Approved, You Get Paid.</p>
  </div>
  <div class="step" style="left:429px">
    <div class="step__photo step__photo--sign" role="img" aria-label="Yellow road sign reading Get Paid to Share against a blue sky"></div>
    <div class="step__title">EVERYBODY BENEFITS<br>FROM REFERRALS</div>
    <p class="step__text">We Provide Expert Quality<br>Work for Affordable Price</p>
  </div>

  <p class="refer-line"><span>REFER :</span> FLOODS, REMODELS, RENOVATIONS &amp; REPAIRS</p>

  <footer class="contact">
    <div class="contact__cta">CALL, TEXT OR BOOK ON-LINE</div>
    <div class="contact__phone"><span>NE</span>858-471-6093</div>
    <div class="contact__rule"></div>
    <div class="contact__web">www.BrightlaneRenovate.com</div>
  </footer>
</section>

</body>
</html>
```